Website for new crypto research organization

See brief (attached). This is a pretty basic website with only a handful of pages + ability to collect email addresses.

```html
<!DOCTYPE html>
<html lang="en">
<head>
<meta charset="utf-8">
<title>Tidewell Labs – Crypto Research website, two homepage layouts</title>
<link rel="stylesheet" href="https://fonts.googleapis.com/css2?family=Rubik:wght@400;500;600;700&family=Montserrat:ital,wght@0,400;0,500;0,600;1,400&display=swap">
<style>
:root{
  --board:#878787;
  --white:#ffffff;
  --ink:#14212c;
  --teal:#1a9aa6;
  --blue:#2396cf;
  --accent:#2397c9;
  --navy:#0f1c26;
  --muted:#5b6670;
  --mist:#eef1f4;
}
*{box-sizing:border-box;margin:0;padding:0}
html,body{width:1008px;height:1200px;overflow:hidden}
body{background:var(--board);font-family:"Montserrat",sans-serif;color:var(--ink);position:relative}

.page{position:absolute;top:77px;width:436px;background:var(--white);overflow:hidden;box-shadow:0 4px 18px rgba(0,0,0,.25)}
.page--grid{left:60px;height:1047px}
.page--carousel{left:512px;height:1003px}

/* header */
.brand{position:absolute;left:53px;top:8px;width:84px;height:40px;display:flex;align-items:center;gap:5px}
.brand__mark{width:9px;height:9px;background:var(--teal);flex:none}
.brand__name{font-family:"Rubik",sans-serif;font-weight:600;font-size:12px;line-height:1;color:var(--teal);letter-spacing:.3px}
.call{position:absolute;left:265px;top:8px;display:flex;align-items:center;gap:4px;font-family:"Rubik",sans-serif;font-weight:600;font-size:9.5px}
.nav{position:absolute;left:174px;top:33px;display:flex;gap:14px;font-family:"Rubik",sans-serif;font-size:6.8px;font-weight:500}
.nav a{color:var(--ink);text-decoration:none;position:relative}
.nav a.is-active::after{content:"";position:absolute;left:0;right:0;bottom:-4px;height:1.5px;background:var(--teal)}

/* torn bands */
.torn{clip-path:polygon(0 3px,6% 0,11% 4px,19% 1px,27% 4px,35% 0,44% 3px,52% 1px,61% 4px,70% 0,78% 3px,87% 1px,94% 4px,100% 1px,100% calc(100% - 3px),93% 100%,85% calc(100% - 4px),76% calc(100% - 1px),67% calc(100% - 4px),58% 100%,49% calc(100% - 3px),40% calc(100% - 1px),31% calc(100% - 4px),22% 100%,13% calc(100% - 3px),5% calc(100% - 1px),0 calc(100% - 4px))}

.hero{position:absolute;left:2px;right:2px;top:54px;height:165px}
.hero__bg{position:absolute;inset:0}
.page--grid .hero__bg{background:radial-gradient(ellipse at 30% 50%,#1d5c66 0%,#0f2e36 45%,#071419 100%)}
.page--carousel .hero__bg{background:linear-gradient(100deg,#6b4a3a 0%,#3d6a86 20%,#8a3f7a 40%,#c48a2c 55%,#4c3b6e 72%,#7b4b3b 88%,#3a4f5c 100%)}
.hero__bg::after{content:"";position:absolute;inset:0;background:rgba(0,0,0,.35)}
.hero__title{position:absolute;left:112px;top:43px;width:207px;height:27px;background:var(--teal);color:var(--white);font-family:"Rubik",sans-serif;font-weight:500;font-size:20px;display:flex;align-items:center;justify-content:center;letter-spacing:.2px}
.hero__lead{position:absolute;left:0;right:0;top:78px;text-align:center;color:var(--white);font-family:"Rubik",sans-serif;font-weight:500;font-size:10.5px;text-shadow:0 1px 2px rgba(0,0,0,.6)}
.hero__cta{position:absolute;left:155px;top:102px;width:122px;height:23px;border:1px solid var(--white);color:var(--white);font-family:"Rubik",sans-serif;font-weight:500;font-size:6.4px;display:flex;align-items:center;justify-content:center;background:rgba(0,0,0,.25)}
.hero__scroll{position:absolute;left:402px;top:112px}

/* section headings */
.heading{position:absolute;left:0;right:0;text-align:center;font-family:"Rubik",sans-serif;font-weight:600;font-size:19px;letter-spacing:.2px}
.heading .hl{color:var(--accent)}

/* news */
.news-bg{position:absolute;left:0;right:0;background:linear-gradient(180deg,#fff 0%,var(--mist) 50%,#fff 100%)}
.date{position:absolute;width:18px;height:20px;background:var(--teal);color:var(--white);font-family:"Rubik",sans-serif;font-weight:600;font-size:5.8px;line-height:1.25;display:flex;flex-direction:column;align-items:center;justify-content:center}
.card{position:absolute;top:297px;width:107px}
.card__img{position:absolute;left:0;top:0;width:107px;height:87px}
.img-a{background:linear-gradient(135deg,#2c4c55,#0d1f26 60%,#3d6a3d)}
.img-b{background:linear-gradient(150deg,#1d2a34,#0b141b 55%,#5a3a1f)}
.img-c{background:linear-gradient(135deg,#6a7b8a,#2c3c4c 55%,#1a5870)}
.card__title{font-family:"Rubik",sans-serif;font-weight:500;font-size:6.3px;line-height:1.3;text-transform:uppercase}
.card__text{font-size:4.3px;line-height:1.8;color:var(--muted);letter-spacing:-.05px}
.btn{display:flex;align-items:center;justify-content:center;border:1px solid var(--blue);color:var(--blue);font-family:"Rubik",sans-serif;font-weight:600;font-size:5.3px;background:var(--white)}

.page--grid .card__panel{position:absolute;left:9px;top:68px;width:89px;background:var(--white);padding-top:8px;text-align:center}
.page--grid .card__text{margin-top:6px;width:101px;margin-left:-6px}
.page--grid .card .btn{position:absolute;left:26px;top:134px;width:55px;height:19px}
.page--grid .date{left:83px;top:6px}

.page--carousel .card{height:110px;background:var(--white);box-shadow:0 1px 4px rgba(0,0,0,.08)}
.page--carousel .card__body{padding:19px 9px 0;width:107px}
.page--carousel .card__text{margin-top:6px;width:89px}
.page--carousel .card .btn{position:absolute;left:9px;top:74px;width:55px;height:19px}
.page--carousel .date{left:83px;top:6px}
.card--feature .card__img{height:110px}
.card--feature .card__img::after{content:"";position:absolute;inset:0;background:linear-gradient(180deg,rgba(35,150,207,.1) 30%,rgba(35,150,207,.9) 100%)}
.card--feature .card__title{position:absolute;left:0;right:0;top:81px;text-align:center;color:var(--white)}

.arrows{position:absolute;left:199px;display:flex;gap:3px}
.arrow{width:17px;height:17px;border:1px solid #8a96a0;border-radius:50%;background:var(--white);display:flex;align-items:center;justify-content:center}

/* research band */
.research{position:absolute;left:2px;right:2px;height:204px;background:linear-gradient(135deg,var(--teal) 0%,var(--blue) 100%);color:var(--white)}
.research__photo{position:absolute;left:30px;width:156px;height:156px;border-radius:50%;background:radial-gradient(circle at 45% 40%,#3a4e6a,#16253a 70%);box-shadow:0 0 0 3px rgba(15,28,38,.35)}
.research__title{position:absolute;left:205px;font-family:"Rubik",sans-serif;font-weight:600;font-size:19px;line-height:1.07}
.research__text{position:absolute;left:205px;width:175px;font-size:4.7px;line-height:1.85}
.research .btn{position:absolute;left:205px;width:55px;height:20px;border-color:var(--white);color:var(--white);background:transparent}

/* newsletter */
.newsletter__text{position:absolute;left:70px;right:70px;text-align:center;font-size:5.7px;line-height:1.85;color:var(--muted)}
.newsletter .btn{position:absolute;left:183px;width:70px;height:24px;font-size:6.6px;background:transparent}

/* footer */
.footer{position:absolute;left:2px;right:2px;bottom:0;background:var(--navy);color:var(--white);clip-path:polygon(0 4px,8% 1px,17% 4px,26% 0,35% 3px,45% 1px,54% 4px,63% 0,72% 3px,81% 1px,90% 4px,100% 0,100% 100%,0 100%)}
.footer .brand{left:51px;width:96px;height:54px}
.footer__nav{position:absolute;left:161px;display:flex;gap:5px;font-family:"Rubik",sans-serif;font-weight:500;font-size:5.8px;letter-spacing:.1px}
.footer__nav span.sep{opacity:.8}
.footer__legal{position:absolute;left:161px;font-size:5.2px;opacity:.9}
.footer__social{position:absolute;left:161px;display:flex;gap:5px}
.footer__social span{width:20px;height:20px;border-radius:50%;border:1px solid rgba(255,255,255,.8)}
.footer__disclaimer{position:absolute;left:70px;right:70px;text-align:center;font-size:4.6px;line-height:1.7;font-style:italic}
.footer__disclaimer b{font-style:normal}
</style>
</head>
<body>

<!-- ========== Layout A: news grid ========== -->
<section class="page page--grid" aria-label="Homepage layout with news grid">
  <header>
    <div class="brand"><span class="brand__mark"></span><span class="brand__name">TIDEWELL LABS</span></div>
    <div class="call">
      <svg width="16" height="16" viewBox="0 0 16 16"><circle cx="8" cy="8" r="7" fill="none" stroke="#1a9aa6" stroke-width="1.3"/><path d="M5.3 4.6l1.4-.2.8 1.8-.9.7c.4.9 1.1 1.6 2 2l.7-.9 1.8.8-.2 1.4c-3 .4-6-2.6-5.6-5.6z" fill="#1a9aa6"/></svg>
      <span>Call : +1 555 010 0100</span>
    </div>
    <nav class="nav"><a class="is-active">Home</a><a>About</a><a>Research</a><a>News</a><a>Careers</a><a>Contact</a></nav>
  </header>

  <div class="hero torn">
    <div class="hero__bg" role="img" aria-label="Dark teal photo of hands on a laptop with trading charts"></div>
    <h1 class="hero__title">CRYPTO RESEARCH</h1>
    <p class="hero__lead">Sed ut perspiciatis unde omnis iste nauptatem</p>
    <div class="hero__cta">RECENT RESEARCH REPORTS</div>
    <svg class="hero__scroll" width="10" height="22" viewBox="0 0 10 22"><rect x="1.5" y="1" width="7" height="11" rx="3.5" fill="none" stroke="#fff"/><line x1="5" y1="3.5" x2="5" y2="5.5" stroke="#fff"/><path d="M1.5 16l3.5 3 3.5-3" fill="none" stroke="#fff"/></svg>
  </div>

  <div class="news-bg" style="top:228px;height:280px"></div>
  <h2 class="heading" style="top:254px"><span class="hl">RECENT</span> NEWS</h2>

  <article class="card" style="left:53px">
    <div class="card__img img-a" role="img" aria-label="Hands typing on a laptop with charts"></div>
    <div class="date">FEB<span>2022</span></div>
    <div class="card__panel">
      <h3 class="card__title">Nemo enim ipsam<br>voluptatem</h3>
      <p class="card__text">Lorem ipsum dolor sit ametonsectetur adipiscing elit, sed do eiusmod tempor incididunt ut labore et dolore</p>
    </div>
    <div class="btn">READ MORE</div>
  </article>
  <article class="card" style="left:165px">
    <div class="card__img img-b" role="img" aria-label="Phone showing a price chart at night"></div>
    <div class="date">FEB<span>2022</span></div>
    <div class="card__panel">
      <h3 class="card__title">Excepteur sinocca<br>ecat cupidatat</h3>
      <p class="card__text">Lorem ipsum dolor sit ametonsectetur adipiscing elit, sed do eiusmod tempor incididunt ut labore et dolore</p>
    </div>
    <div class="btn">READ MORE</div>
  </article>
  <article class="card" style="left:277px">
    <div class="card__img img-c" role="img" aria-label="Desk with coffee, notes and a keyboard"></div>
    <div class="date">FEB<span>2022</span></div>
    <div class="card__panel">
      <h3 class="card__title">Duis aute irure<br>dolorin</h3>
      <p class="card__text">Lorem ipsum dolor sit ametonsectetur adipiscing elit, sed do eiusmod tempor incididunt ut labore et dolore</p>
    </div>
    <div class="btn">READ MORE</div>
  </article>
  <div class="arrows" style="top:467px">
    <span class="arrow"><svg width="6" height="8" viewBox="0 0 6 8"><path d="M4.5 1L1.5 4l3 3" fill="none" stroke="#14212c" stroke-width="1"/></svg></span>
    <span class="arrow"><svg width="6" height="8" viewBox="0 0 6 8"><path d="M1.5 1l3 3-3 3" fill="none" stroke="#14212c" stroke-width="1"/></svg></span>
  </div>

  <section class="research torn" style="top:512px">
    <div class="research__photo" role="img" aria-label="Team of analysts reviewing documents in an office at night" style="top:25px"></div>
    <h2 class="research__title" style="top:40px">RESEARCH<br>PROCESS</h2>
    <p class="research__text" style="top:89px">Lorem ipsum dolor sit amet, consectetur adipiscing elit, sed do eiusmod tempor incididunt ut labore et dolore magna aliqua. Quis ipsum suspendisse ultrices gravida. Risus commodos accumsan lacus vel facilisis. Lorem ipsum dolor sit amet, consectetur adipiscing elit, sed do eiusmod tempor incididunt ut labore et dolore magna aliqis ipsum suspendisse</p>
    <div class="btn" style="top:145px">READ MORE</div>
  </section>

  <section class="newsletter">
    <div class="news-bg" style="top:720px;height:170px"></div>
    <h2 class="heading" style="top:756px"><span class="hl">SUBSCRIBE TO</span> NEWSLETTER</h2>
    <p class="newsletter__text" style="top:791px">Lorem ipsum dolor sit amet, consectetur adipiscing elit, sed do eiusmod tempor incididunt ut labore et dolore magna s ipsum suspendisse ultrices grcomcenas accumsan lacus vel facilisis.</p>
    <div class="btn" style="top:827px">SUBSCRIBE</div>
  </section>

  <footer class="footer" style="height:155px">
    <div class="brand" style="top:30px"><span class="brand__mark"></span><span class="brand__name">TIDEWELL LABS</span></div>
    <nav class="footer__nav" style="top:30px"><span>HOME</span><span class="sep">/</span><span>ABOUT</span><span class="sep">/</span><span>RESEARCH</span><span class="sep">/</span><span>NEWS</span><span class="sep">/</span><span>CAREERS</span><span class="sep">/</span><span>CONTACT</span></nav>
    <p class="footer__legal" style="top:49px">© 2022 Tidewell Labs. All rights reserved | Privacy | Terms of Use</p>
    <div class="footer__social" style="top:66px" aria-label="Social links"><span></span><span></span><span></span></div>
    <p class="footer__disclaimer" style="top:111px"><b>Disclaimer :</b> Lorem ipsum dolor sit amet, consectetur adipiscing elit, sed do eiusmod tempor incididunt ut labore et dolore magna aliqis ipsum suspendisse ultrices gravidisus commodo viverra maecenas accumsan lacus vel facilisis. Lorem ipsum dolor sit amet, consectetur adipiscing elit, sed do eiusmod tempor incididunt ut labore et dolore magna aliqis ipsum</p>
  </footer>
</section>

<!-- ========== Layout B: news carousel ========== -->
<section class="page page--carousel" aria-label="Homepage layout with news carousel">
  <header>
    <div class="brand"><span class="brand__mark"></span><span class="brand__name">TIDEWELL LABS</span></div>
    <div class="call">
      <svg width="16" height="16" viewBox="0 0 16 16"><circle cx="8" cy="8" r="7" fill="none" stroke="#1a9aa6" stroke-width="1.3"/><path d="M5.3 4.6l1.4-.2.8 1.8-.9.7c.4.9 1.1 1.6 2 2l.7-.9 1.8.8-.2 1.4c-3 .4-6-2.6-5.6-5.6z" fill="#1a9aa6"/></svg>
      <span>Call : +1 555 010 0100</span>
    </div>
    <nav class="nav"><a class="is-active">Home</a><a>About</a><a>Research</a><a>News</a><a>Careers</a><a>Contact</a></nav>
  </header>

  <div class="hero torn">
    <div class="hero__bg" role="img" aria-label="Colourful street wall covered in graffiti"></div>
    <h1 class="hero__title">CRYPTO RESEARCH</h1>
    <p class="hero__lead">Sed ut perspiciatis unde omnis iste nauptatem</p>
    <div class="hero__cta">RECENT RESEARCH REPORTS</div>
    <svg class="hero__scroll" width="10" height="22" viewBox="0 0 10 22"><rect x="1.5" y="1" width="7" height="11" rx="3.5" fill="none" stroke="#fff"/><line x1="5" y1="3.5" x2="5" y2="5.5" stroke="#fff"/><path d="M1.5 16l3.5 3 3.5-3" fill="none" stroke="#fff"/></svg>
  </div>

  <div class="news-bg" style="top:228px;height:240px"></div>
  <h2 class="heading" style="top:254px"><span class="hl">RECENT</span> NEWS</h2>

  <article class="card" style="left:53px">
    <div class="date">FEB<span>2022</span></div>
    <div class="card__body">
      <h3 class="card__title">Nemo enim ipsam<br>voluptatem</h3>
      <p class="card__text">Lorem ipsum dolor sit ametonsectetur adipiscing elit, sed do eiusmod tempor incididunt ut labore et dolore</p>
    </div>
    <div class="btn">READ MORE</div>
  </article>
  <article class="card card--feature" style="left:165px">
    <div class="card__img img-b" role="img" aria-label="Phone showing a price chart at night"></div>
    <div class="date">FEB<span>2022</span></div>
    <h3 class="card__title">Excepteur sinocca<br>ecat cupidatat</h3>
  </article>
  <article class="card" style="left:277px">
    <div class="date">FEB<span>2022</span></div>
    <div class="card__body">
      <h3 class="card__title">Duis aute irure<br>dolorin</h3>
      <p class="card__text">Lorem ipsum dolor sit ametonsectetur adipiscing elit, sed do eiusmod tempor incididunt ut labore et dolore</p>
    </div>
    <div class="btn">READ MORE</div>
  </article>
  <div class="arrows" style="top:424px">
    <span class="arrow"><svg width="6" height="8" viewBox="0 0 6 8"><path d="M4.5 1L1.5 4l3 3" fill="none" stroke="#14212c" stroke-width="1"/></svg></span>
    <span class="arrow"><svg width="6" height="8" viewBox="0 0 6 8"><path d="M1.5 1l3 3-3 3" fill="none" stroke="#14212c" stroke-width="1"/></svg></span>
  </div>

  <section class="research torn" style="top:469px">
    <div class="research__photo" role="img" aria-label="Team of analysts reviewing documents in an office at night" style="top:21px"></div>
    <h2 class="research__title" style="top:37px">RESEARCH<br>PROCESS</h2>
    <p class="research__text" style="top:86px">Lorem ipsum dolor sit amet, consectetur adipiscing elit, sed do eiusmod tempor incididunt ut labore et dolore magna aliqua. Quis ipsum suspendisse ultrices gravida. Risus commodos accumsan lacus vel facilisis. Lorem ipsum dolor sit amet, consectetur adipiscing elit, sed do eiusmod tempor incididunt ut labore et dolore magna aliqis ipsum suspendisse</p>
    <div class="btn" style="top:143px">READ MORE</div>
  </section>

  <section class="newsletter">
    <div class="news-bg" style="top:676px;height:170px"></div>
    <h2 class="heading" style="top:712px"><span class="hl">SUBSCRIBE TO</span> NEWSLETTER</h2>
    <p class="newsletter__text" style="top:747px">Lorem ipsum dolor sit amet, consectetur adipiscing elit, sed do eiusmod tempor incididunt ut labore et dolore magna s ipsum suspendisse ultrices grcomcenas accumsan lacus vel facilisis.</p>
    <div class="btn" style="top:783px">SUBSCRIBE</div>
  </section>

  <footer class="footer" style="height:157px">
    <div class="brand" style="top:32px"><span class="brand__mark"></span><span class="brand__name">TIDEWELL LABS</span></div>
    <nav class="footer__nav" style="top:33px"><span>HOME</span><span class="sep">/</span><span>ABOUT</span><span class="sep">/</span><span>RESEARCH</span><span class="sep">/</span><span>NEWS</span><span class="sep">/</span><span>CAREERS</span><span class="sep">/</span><span>CONTACT</span></nav>
    <p class="footer__legal" style="top:52px">© 2022 Tidewell Labs. All rights reserved | Privacy | Terms of Use</p>
    <div class="footer__social" style="top:70px" aria-label="Social links"><span></span><span></span><span></span></div>
    <p class="footer__disclaimer" style="top:114px"><b>Disclaimer :</b> Lorem ipsum dolor sit amet, consectetur adipiscing elit, sed do eiusmod tempor incididunt ut labore et dolore magna aliqis ipsum suspendisse ultrices gravidisus commodo viverra maecenas accumsan lacus vel facilisis. Lorem ipsum dolor sit amet, consectetur adipiscing elit, sed do eiusmod tempor incididunt ut labore et dolore magna aliqis ipsum</p>
  </footer>
</section>

</body>
</html>
```